Bramblewick Forage Business Cards

I need a business card with my logo, number, Facebook account, and some information about what I am selling. Green card with logo on the front. 555-214-8392 phone number, @bramblewickforage Facebook, •Orchardgrass Hay •Alfalfa Hay •Mixed Grass Hay , and “Premium Quality Hay” all written on the back.

Target Market(s)

Hay

Contact Information for Business Card

Phone number, Facebook, different types of hay.

Colors
00AB8E
00BBA5
67D7C9
C6EFE9
E9F9F6

```html
<!DOCTYPE html>
<html lang="en">
<head>
<meta charset="utf-8">
<title>Bramblewick Forage Business Cards</title>
<link rel="stylesheet" href="https://fonts.googleapis.com/css2?family=Yellowtail&family=Roboto:wght@400;500;700&display=swap">
<style>
  :root {
    --backdrop: #2b2b2b;
    --card: #151515;
    --emboss: #1d1d1d;
    --emboss-ink: #262626;
    --ink: #f2f2f2;
    --ink-soft: #d9d9d9;
    --leaf: #3f9e45;
  }
  * { box-sizing: border-box; margin: 0; padding: 0; }
  html, body {
    width: 1200px;
    height: 868px;
    overflow: hidden;
    background: var(--backdrop);
  }
  .stage {
    position: relative;
    width: 1200px;
    height: 868px;
  }
  .card {
    position: absolute;
    top: 291px;
    width: 500px;
    height: 286px;
    overflow: hidden;
    background: var(--card);
    border-radius: 3px;
    box-shadow: 0 10px 28px rgba(0,0,0,.45);
    color: var(--ink);
    font-family: 'Roboto', sans-serif;
  }
  .card--front { left: 70px; }
  .card--back { left: 630px; }

  .brand-mark {
    position: absolute;
    left: 62px;
    top: 76px;
    width: 84px;
    height: 84px;
    border-radius: 50%;
    background: var(--leaf);
  }
  .brand-name {
    font-family: 'Yellowtail', cursive;
    font-weight: 400;
    color: var(--ink);
    white-space: nowrap;
    line-height: 1.1;
  }
  .card--front .brand-name {
    position: absolute;
    left: 160px;
    top: 66px;
    font-size: 34px;
  }
  .card--front .phone {
    position: absolute;
    left: 164px;
    top: 112px;
    font-size: 32px;
    font-weight: 700;
    letter-spacing: .5px;
    white-space: nowrap;
  }
  .products {
    position: absolute;
    left: 0;
    right: 0;
    bottom: 44px;
    text-align: center;
    font-size: 13px;
    color: var(--ink-soft);
    letter-spacing: .2px;
    white-space: nowrap;
  }
  .products .dot {
    display: inline-block;
    width: 6px;
    height: 6px;
    margin: 0 6px 1px;
    border-radius: 50%;
    background: var(--leaf);
  }

  .emboss-mark {
    position: absolute;
    right: 56px;
    top: 34px;
    width: 140px;
    height: 140px;
    border-radius: 50%;
    background: var(--emboss);
  }
  .emboss-name {
    position: absolute;
    right: 36px;
    top: 186px;
    font-size: 20px;
    font-weight: 500;
    color: var(--emboss-ink);
    white-space: nowrap;
  }
  .contact {
    position: absolute;
    left: 40px;
    top: 118px;
  }
  .card--back .brand-name {
    display: inline-block;
    font-size: 30px;
    padding: 0 6px 2px 0;
    border-bottom: 1.5px solid var(--ink-soft);
  }
  .card--back .phone {
    margin-top: 4px;
    font-size: 28px;
    font-weight: 700;
    letter-spacing: .5px;
    white-space: nowrap;
  }
  .social {
    display: flex;
    align-items: center;
    gap: 8px;
    margin-top: 2px;
    font-size: 20px;
    color: var(--ink-soft);
    white-space: nowrap;
  }
  .social .badge {
    width: 20px;
    height: 20px;
    border-radius: 50%;
    background: var(--ink-soft);
  }
</style>
</head>
<body>
  <main class="stage">
    <section class="card card--front" aria-label="Card front">
      <div class="brand-mark" aria-hidden="true"></div>
      <h1 class="brand-name">Bramblewick Forage</h1>
      <p class="phone">555-214-8392</p>
      <p class="products">Orchardgrass Hay<span class="dot"></span>Alfalfa Hay<span class="dot"></span>Mixed Grass Hay, &amp; Premium Quality Hay</p>
    </section>

    <section class="card card--back" aria-label="Card back">
      <div class="emboss-mark" role="img" aria-label="Blind-embossed brand mark"></div>
      <p class="emboss-name" aria-hidden="true">Bramblewick Forage</p>
      <div class="contact">
        <h2 class="brand-name">Bramblewick Forage</h2>
        <p class="phone">555-214-8392</p>
        <p class="social"><span class="badge" aria-hidden="true"></span>@bramblewickforage</p>
      </div>
    </section>
  </main>
</body>
</html>
```